Attorney Website Home Page Design Project

I am starting my law firm and I need a website design. I am going to be practicing in the field of personal injury, and I need a website design that conveys reliability and professionalism, but is still personable. This website will mostly be accessed by potential clients looking for information about me, and my potential clients are individual people, not businesses.

I have a logo that I just had designed by a designer on this site that I will be using. The colors used int he site should be complementary to the ones in that logo. Also, I have listed three websites that I want to base the overall look of my site on. This does NOT mean I want to copy them- instead, I am listing them for inspiration and to better convey what I am looking for.

Please use filler text and filler images for everything, and structure the menus as I have described below.

I will be taking this design- as a PSD file- and having it converted in to HTML, so I will need a perfect, multi-layered PSD file when completed.

I also will need a contact form that is consistent on every page.

Overall design on this site is up to you. See the attached logo files for inspiration on the color scheme. I am looking for a professional but personal website for my law firm. Check out the sites below for inspiration.

I. Websites for inspiration:

www.DonovanKemptLaw.com THIS IS WHERE I WANT ABOUT 50% OF YOUR INSPIRATION TO COME FROM

www.OkaforPersonalInjury.com 25%

www.VelmorAdvocate.com 25%

I want all aspects of this site- menu panels and what not to be expandable and done in full uncompressed photoshop psd format so I can have them converted to html, and then in to a full site.

See the attached logo- the colors in it should direct the overall color scheme of the site.

I want you to use placeholder text and placeholder images- you can use white boxes with text in them that says what type of image should be used in its place. I also want a placeholder for a video on the home page.

II. Menu structure:

A. Main Menu and Submenu Items:

Our Purpose

What An Attorney Does

Why Choose Quillbrook Attorneys

No Fee Guarantee

Cases We Handle (Below is a partial list- take the whole list from DonovanKemptLaw.com

Auto Accidents

Slip and Fall Injuries

Dog Bites

Animal Bites

General Injury Cases

Your Case

How Are You Feeling?

What You Should Be Doing

Talk To Us

Contact Us

Target Market(s)

Injured people who need an attorney. Individuals, not companies.

Industry/Entity Type

Law Firm

Requirements
Must have
• Must be themed according to the websites I have listed and in line with my logo.

Must convey reliability, professionalism and warmth.

Must appeal to an individual person- I am practicing personal injury, not corporate or business law.

Must have one eye-catching item- "Contact Us Now to Get These Questions Answered:" with a 10 item numbered list of questions.
Should not have
• The site should not be cluttered or difficult to follow.

It should not be elitist or look like it is designed for corporate law.

```html
<!DOCTYPE html>
<html lang="en">
<head>
<meta charset="utf-8">
<title>Quillbrook Attorneys – Home</title>
<link href="https://fonts.googleapis.com/css2?family=Open+Sans:wght@300;400;600&family=Libre+Baskerville:wght@400;700&display=swap" rel="stylesheet">
<style>
:root{
  --navy:#1d3f73;
  --blue:#0d4f8a;
  --blue-dark:#0a3866;
  --blue-light:#2a7fc0;
  --link:#1a7ac4;
  --accent-cyan:#1aa3dc;
  --orange:#e0622a;
  --text:#444;
  --heading:#3a3a3a;
  --hero-bg:#e9eaec;
  --rule:#dcdcdc;
  --footer:#2b2b2b;
  --footer-text:#b9b9b9;
  --white:#fff;
}
*{margin:0;padding:0;box-sizing:border-box}
html,body{width:987px;height:1200px;overflow:hidden}
body{position:relative;background:var(--white);font-family:Arial,Helvetica,sans-serif;color:var(--text)}
.abs{position:absolute}
.logo{font-family:"Libre Baskerville",serif;font-weight:400;color:var(--navy);font-size:25px;letter-spacing:.5px;white-space:nowrap}
.call-box{left:529px;top:0;width:299px;height:72px;border-radius:0 0 4px 4px;background:linear-gradient(180deg,#1f6aa6,#0b3f70);color:var(--white);text-align:center;font-family:"Libre Baskerville",serif;white-space:nowrap}
.call-box .label{font-size:15px;margin-top:6px}
.call-box .phone{font-size:34px;font-weight:700;line-height:42px}
.hero{left:0;top:82px;width:987px;height:379px;background:linear-gradient(180deg,#eeeff1,#e2e3e6)}
.hero-photo{left:165px;top:90px;width:315px;height:371px;background:linear-gradient(180deg,#dfe1e5 0%,#c9ccd2 45%,#4a4f5a 80%,#22252c 100%)}
.nav{left:420px;top:95px;width:414px;height:39px;border-radius:4px;background:linear-gradient(180deg,#1e6aa8,#0b3f72);display:flex;align-items:center;font-size:11px;color:var(--white);font-family:"Open Sans",sans-serif;white-space:nowrap;overflow:hidden}
.nav span{flex:none;padding:0 9px;border-right:1px solid rgba(255,255,255,.25);line-height:39px}
.nav .lang{flex:1;display:flex;align-items:center;gap:10px;border-right:0;background:rgba(0,0,0,.15);margin:0 4px 0 2px;height:30px;line-height:30px;border-radius:3px}
.nav .flag{width:16px;height:10px;background:#c8d3e6;border:1px solid #fff}
.nav .caret{margin-left:auto;font-size:8px}
.contact-frame{left:609px;top:139px;width:213px;height:271px;border-radius:6px;background:#c9cdd2}
.contact-panel{left:616px;top:146px;width:199px;height:257px;border-radius:4px;background:linear-gradient(160deg,#1b5d99 0%,#0c3c6c 60%,#1a5a94 100%)}
.contact-panel h2{font-family:"Open Sans",sans-serif;font-weight:600;font-size:20px;color:var(--white);text-align:center;margin-top:14px}
.field{left:8px;width:182px;background:var(--white);border-radius:3px;font-size:7.5px;color:#999;padding:7px 8px}
.field.select{background:#e8ecf1}
.field .drop{position:absolute;right:4px;top:4px;width:14px;height:14px;border-radius:2px;background:#7fb1de}
.btn-grey{left:119px;top:229px;width:66px;height:20px;border-radius:3px;background:linear-gradient(#fff,#d7d7d7);font-size:9px;font-weight:bold;color:#333;text-align:center;line-height:20px}
.thumb{top:420px;width:43px;height:32px;border:2px solid var(--white);box-shadow:0 0 2px #999}
h3.col-title{font-family:"Open Sans",sans-serif;font-weight:400;font-size:19px;color:var(--heading)}
.copy{font-size:9.6px;line-height:16.4px;color:var(--text)}
.justify{text-align:justify}
.btn-blue{width:71px;height:22px;border-radius:3px;background:linear-gradient(#1d66a6,#0c3f73);color:var(--white);font-size:10px;font-weight:bold;text-align:center;line-height:22px;border:1px solid #0a2f57}
.img-ph{border:1px solid var(--rule);padding:2px;background:var(--white)}
.img-ph div{width:100%;height:100%}
.practice-title{font-size:11.5px;color:var(--link)}
.practice-rule{left:387px;width:212px;height:1px;background:var(--rule)}
.video{left:614px;top:523px;width:213px;height:121px;background:linear-gradient(135deg,#3b3a3a,#6b5a4d 50%,#2c2c2c);border:2px solid #222}
.video .play{position:absolute;left:94px;top:46px;width:24px;height:16px;background:#111;border-radius:2px}
.video .play:after{content:"";position:absolute;left:9px;top:4px;border-left:7px solid #fff;border-top:4px solid transparent;border-bottom:4px solid transparent}
.video .bar{position:absolute;left:0;bottom:0;width:100%;height:10px;background:#111}
.video .bar i{position:absolute;left:0;top:0;width:50px;height:2px;background:#c0282d}
.purpose{left:162px;top:790px;width:663px;height:111px;border:1px solid var(--rule);border-radius:5px;background:linear-gradient(#fff,#f4f4f4)}
.purpose-col{top:10px;width:182px}
.purpose-col h4{font-family:"Open Sans",sans-serif;font-weight:400;font-size:16.5px;color:var(--heading);margin-bottom:4px;white-space:nowrap}
.purpose-col h4.cyan{color:var(--accent-cyan)}
.purpose-col .copy{font-size:9px;line-height:12.8px}
.read-more{font-size:9px;color:var(--orange);text-align:right;margin-top:6px;padding-right:18px}
.purpose-div{top:0;width:1px;height:109px;background:linear-gradient(#fff,#ddd,#fff)}
.faq-tag{left:860px;top:762px;width:100px;text-align:center;font-size:10.5px;line-height:13.5px;color:var(--link)}
.faq-person{left:900px;top:810px;width:87px;height:110px;background:linear-gradient(180deg,#e4e6ea,#9aa0aa 60%,#3a3e46)}
.click-here{left:837px;top:890px;width:110px;height:24px;border-radius:4px;background:linear-gradient(#2586c8,#0c4a80);color:var(--white);font-family:"Open Sans",sans-serif;font-size:14px;text-align:center;line-height:24px}
.footer{left:0;top:920px;width:987px;height:280px;background:var(--footer)}
.foot-title{font-family:"Open Sans",sans-serif;font-weight:400;font-size:16px;color:var(--white);white-space:nowrap}
.badge{width:52px;height:51px;border:2px solid #ddd;background:#6b1f15}
.foot-btn{width:67px;height:21px;border-radius:3px;background:linear-gradient(#1e6aa8,#0c3f73);color:var(--white);font-size:10px;font-weight:bold;text-align:center;line-height:21px}
.arrows{left:395px;top:957px;font-size:16px;color:#777;letter-spacing:8px}
.office{left:474px;font-size:9.6px;color:#ddd}
.office.row{display:flex;width:162px;justify-content:space-between}
.social-icon{left:679px;width:28px;height:28px;border-radius:5px;background:#5a5a5a}
.social-label{left:723px;font-size:10.5px;color:#ccc}
.legal{right:162px;top:1161px;font-size:9px;line-height:14px;color:#999;text-align:right}
</style>
</head>
<body>

<header>
  <div class="abs logo" style="left:172px;top:24px">Quillbrook Attorneys</div>
  <div class="abs call-box">
    <div class="label">Call for a FREE CONSULTATION</div>
    <div class="phone">(800)555-0182</div>
  </div>
</header>

<section class="abs hero" aria-label="Hero"></section>
<div class="abs hero-photo" role="img" aria-label="Portrait photo of the lead attorney"></div>

<nav class="abs nav">
  <span>Our Story</span><span>Your Stories</span><span>Our Services</span><span>Your Case</span>
  <span class="lang"><i class="flag"></i>English<b class="caret">&#9660;</b></span>
</nav>

<div class="abs contact-frame"></div>
<form class="abs contact-panel">
  <h2>Contact Us Now</h2>
  <div class="abs field" style="top:47px;height:22px">type your name in here</div>
  <div class="abs field select" style="top:82px;height:22px">select your area of enquiry<i class="drop"></i></div>
  <div class="abs field" style="top:116px;height:103px">type your message here...</div>
  <div class="abs btn-grey">Learn More</div>
</form>

<div class="abs thumb" style="left:586px;background:#b8bec8" role="img" aria-label="Attorney thumbnail"></div>
<div class="abs thumb" style="left:635px;background:#8a909a" role="img" aria-label="Attorney thumbnail"></div>
<div class="abs thumb" style="left:684px;background:#9a8070" role="img" aria-label="Gavel thumbnail"></div>
<div class="abs thumb" style="left:733px;background:#a8aeb8" role="img" aria-label="Attorney thumbnail"></div>
<div class="abs thumb" style="left:782px;background:#c0c4cc" role="img" aria-label="Attorney thumbnail"></div>

<h3 class="abs col-title" style="left:162px;top:482px">Welcome to our site</h3>
<div class="abs img-ph" style="left:162px;top:516px;width:202px;height:78px" role="img" aria-label="Gavel, scales of justice and law book"><div style="background:linear-gradient(135deg,#3a2a1e,#9a7048 55%,#e0d6c8)"></div></div>
<p class="abs copy" style="left:162px;top:601px;width:205px">Lorem ipsum dolor sit amet, consectetur adipi-scing elit. Fusce accumsan, elit a suscipit sagittis, tortor sapien cursus risus, non rhon-cus lectus nunc ac nulla.<br>Aliquam molestie, mi et imperdiet euismod, dui purus auctor tellus, et interdum lacus lectus et ante. Sed accumsan sollicitudin sapien, sit amet adipiscing turpis gravida ac.</p>
<div class="abs btn-blue" style="left:163px;top:743px">Learn More</div>

<h3 class="abs col-title" style="left:387px;top:482px">Practice Areas</h3>
<div class="abs img-ph" style="left:387px;top:516px;width:62px;height:57px" role="img" aria-label="Aircraft accident scene"><div style="background:linear-gradient(#9aa6ad,#5a6468)"></div></div>
<div class="abs practice-title" style="left:462px;top:515px">Aircraft Accident</div>
<p class="abs copy" style="left:462px;top:529px;width:150px;line-height:14.5px">Lorem ipsum dolor sit amet, consectetur adipiscing elit.</p>
<div class="abs practice-rule" style="top:580px"></div>
<div class="abs img-ph" style="left:387px;top:591px;width:62px;height:57px" role="img" aria-label="Damaged red car after an auto accident"><div style="background:linear-gradient(#8a3a3a,#d4382e 50%,#555)"></div></div>
<div class="abs practice-title" style="left:462px;top:589px">Auto Accident</div>
<p class="abs copy" style="left:462px;top:603px;width:150px;line-height:14.5px">Lorem ipsum dolor sit amet, consectetur adipiscing elit.</p>
<div class="abs practice-rule" style="top:654px"></div>
<div class="abs img-ph" style="left:387px;top:665px;width:62px;height:57px" role="img" aria-label="Dog bite injury"><div style="background:linear-gradient(#3c5a2a,#8a6a48 55%,#2d3a20)"></div></div>
<div class="abs practice-title" style="left:462px;top:663px">Dog Bite Injury</div>
<p class="abs copy" style="left:462px;top:677px;width:150px;line-height:14.5px">Lorem ipsum dolor sit amet, consectetur adipiscing elit.</p>
<div class="abs btn-blue" style="left:388px;top:743px">Learn More</div>

<h3 class="abs col-title" style="left:614px;top:482px">Watch Our Video</h3>
<div class="abs video" role="img" aria-label="Video player showing an attorney speaking in an office"><span class="play"></span><span class="bar"><i></i></span></div>
<p class="abs copy justify" style="left:616px;top:659px;width:209px">Sed ut perspiciatis unde omnis iste natus error sit voluptatem accusantium doloremque laudan tium, totam rem aperiam, eaque ipsa quae ab illo inventore veritatis et quasi architecto beatae vitae dicta sunt explicabo. Nemo enim ipsam voluptatem quia voluptas.</p>

<section class="abs purpose">
  <div class="abs purpose-col" style="left:20px">
    <h4 class="cyan">Our Purpose</h4>
    <p class="copy justify">Lorem Ipsum is simply dummy text of the printing and typesetting industry. Lorem Ipsum has been the industry's standard dummy text</p>
    <div class="read-more">Read More &gt;&gt;</div>
  </div>
  <div class="abs purpose-div" style="left:219px"></div>
  <div class="abs purpose-col" style="left:236px">
    <h4>What an Attorney Does</h4>
    <p class="copy justify">Lorem Ipsum is simply dummy text of the printing and typesetting industry. Lorem Ipsum has been the industry's standard dummy text</p>
    <div class="read-more">Read More &gt;&gt;</div>
  </div>
  <div class="abs purpose-div" style="left:437px"></div>
  <div class="abs purpose-col" style="left:456px">
    <h4>Why Choose Us</h4>
    <p class="copy justify">Lorem Ipsum is simply dummy text of the printing and typesetting industry. Lorem Ipsum has been the industry's standard dummy text</p>
    <div class="read-more">Read More &gt;&gt;</div>
  </div>
</section>

<div class="abs faq-tag">Top 10 Questions<br>We Are Asked<br>By Injured People</div>
<div class="abs faq-person" role="img" aria-label="Thoughtful young man with speech bubbles"></div>
<div class="abs click-here">CLICK HERE</div>

<footer class="abs footer"></footer>
<h3 class="abs foot-title" style="left:162px;top:949px">Membership &amp; Accreditation</h3>
<div class="abs arrows">&#8249;&#8250;</div>
<div class="abs badge" style="left:162px;top:980px" role="img" aria-label="Accreditation badge"></div>
<p class="abs copy justify" style="left:228px;top:976px;width:200px;color:var(--footer-text)">Lorem ipsum dolor sit amet, consectetur adipiscing elit. Fusce accumsan, elit a suscipit sagittis, tortor sapien cursus risus, non rhon-cus lectus nunc ac nulla.</p>
<div class="abs foot-btn" style="left:362px;top:1031px">Learn More</div>
<div class="abs badge" style="left:162px;top:1067px" role="img" aria-label="Accreditation badge"></div>
<p class="abs copy justify" style="left:228px;top:1063px;width:200px;color:var(--footer-text)">Lorem ipsum dolor sit amet, consectetur adipiscing elit. Fusce accumsan, elit a suscipit sagittis, tortor sapien cursus risus, non rhon-cus lectus nunc ac nulla.</p>
<div class="abs foot-btn" style="left:362px;top:1118px">Learn More</div>

<h3 class="abs foot-title" style="left:474px;top:941px">Main Office</h3>
<div class="abs logo" style="left:474px;top:972px;font-size:14px;color:#9a9a9a">Quillbrook Attorneys</div>
<div class="abs office" style="top:1000px;line-height:13.5px">412 Larkspur Lane<br>Brookhaven, D11 42QK.</div>
<div class="abs office row" style="top:1033px"><span>Toll - Free:</span><span>+1 800 xxx xxxx</span></div>
<div class="abs office row" style="top:1050px"><span>Telephone:</span><span>+1 800 xxx xxxx</span></div>
<div class="abs office" style="top:1068px">Email : <span style="color:var(--link)">hello@quillbrooklaw.com</span></div>
<div class="abs office" style="top:1097px;font-size:11px;font-weight:bold;color:#fff">Office Hours:</div>
<div class="abs office" style="top:1116px">8:30 a.m. to 5:30 p.m.</div>
<div class="abs office" style="top:1135px">(Pacific), M-F</div>

<h3 class="abs foot-title" style="left:679px;top:941px">Connect with Us</h3>
<div class="abs social-icon" style="top:971px"></div><div class="abs social-label" style="top:979px">Microblog</div>
<div class="abs social-icon" style="top:1003px"></div><div class="abs social-label" style="top:1011px">Social Page</div>
<div class="abs social-icon" style="top:1035px"></div><div class="abs social-label" style="top:1043px">Circles</div>
<div class="abs social-icon" style="top:1067px"></div><div class="abs social-label" style="top:1075px">Video Channel</div>

<div class="abs legal">Copyright © 2012, Quillbrook.<br>All Rights Reserved. | Legal &nbsp;| &nbsp;Privacy Policy</div>

</body>
</html>
```